Business Card Design

I need business cards designed for a new company i have started that makes cakes, particularly themed kids cakes with a really modern design and I would like to have my business cards reflect this. I have attached some photos of cakes I have made and would like some to be used.

Industry/Entity Type

Business

Contact Information for Business Card

Business Name: Tarts and Treats by Maren
Mobile: 0492 815 063
email: maren@tartsandtreatsbymaren.example.au
Instagram: instagram.com/tartsandtreatsbymaren/
Facebook: fb.me/tartsandtreatsbymaren

Colors
e667a6
b768aa
3276b5

Requirements
Must have
• Business Name: Tarts and Treats by Maren
• Mobile: 0492 815 063
• email: maren@tartsandtreatsbymaren.example.au
• Instagram: instagram.com/tartsandtreatsbymaren/
• Facebook: fb.me/tartsandtreatsbymaren
Nice to have
• 2 to 3 pictures of my cakes

```html
<!DOCTYPE html>
<html lang="en">
<head>
<meta charset="utf-8">
<title>Tarts and Treats by Maren — Business Card</title>
<link href="https://fonts.googleapis.com/css2?family=Open+Sans:wght@400;600&family=Tangerine:wght@400&display=swap" rel="stylesheet">
<style>
  :root {
    --pink: #e667a6;
    --pink-soft: #f0a3c9;
    --plum: #b768aa;
    --blue: #3276b5;
    --cream: #fbe3c6;
    --white: #ffffff;
    --backdrop: #e4e6e8;
    --rule: #4a5f7a;
  }
  * { box-sizing: border-box; margin: 0; padding: 0; }
  html, body {
    width: 1200px;
    height: 1200px;
    overflow: hidden;
    background: var(--backdrop);
    font-family: "Open Sans", Arial, sans-serif;
  }
  .canvas { position: relative; width: 1200px; height: 1200px; }

  .card {
    position: absolute;
    left: 196px;
    width: 793px;
    height: 456px;
    border: 5px solid var(--cream);
    overflow: hidden;
  }
  .card--front { top: 73px; background: var(--pink); }
  .card--back { top: 622px; background: var(--white); }

  /* Front */
  .front-pattern {
    position: absolute;
    inset: 0;
    background: radial-gradient(circle at 30% 40%, var(--pink-soft) 0%, var(--pink) 70%);
  }
  .front-badge {
    position: absolute;
    left: 292px;
    top: 118px;
    width: 209px;
    height: 209px;
    transform: rotate(45deg);
    background: var(--white);
    border: 5px solid var(--cream);
    border-radius: 22px;
  }
  .front-badge__content {
    position: absolute;
    left: 396px;
    top: 222px;
    transform: translate(-50%, -50%);
    width: 220px;
    display: flex;
    flex-direction: column;
    align-items: center;
    gap: 8px;
  }
  .front-badge__mark {
    width: 56px;
    height: 56px;
    border-radius: 50%;
    background: var(--blue);
  }
  .front-badge__name {
    text-align: center;
    color: var(--pink);
    font-family: "Tangerine", "Times New Roman", cursive;
    font-size: 40px;
    line-height: 0.95;
  }

  /* Back */
  .back-mobile {
    position: absolute;
    right: 21px;
    top: 26px;
    color: var(--plum);
    font-size: 17px;
  }
  .brand {
    position: absolute;
    left: 0;
    right: 0;
    top: 78px;
    text-align: center;
    color: var(--pink);
    font-family: "Tangerine", "Times New Roman", cursive;
  }
  .brand__mark {
    display: block;
    width: 150px;
    height: 150px;
    margin: 0 auto 6px;
    border-radius: 50%;
    background: var(--blue);
  }
  .brand__name { font-size: 84px; line-height: 1; }
  .brand__byline {
    display: flex;
    align-items: center;
    justify-content: center;
    gap: 18px;
    margin-top: -6px;
    font-size: 44px;
    line-height: 1;
  }
  .brand__rule { width: 150px; height: 1px; background: var(--rule); }

  .contact-band {
    position: absolute;
    left: 0;
    right: 0;
    bottom: 0;
    height: 40px;
    background: var(--pink);
    display: flex;
    align-items: center;
    justify-content: space-between;
    padding: 0 10px;
    color: var(--white);
    font-size: 12.5px;
    white-space: nowrap;
  }
  .contact-item { display: flex; align-items: center; gap: 5px; }
  .contact-item__dot {
    width: 12px; height: 12px; border-radius: 2px; background: var(--white);
  }
</style>
</head>
<body>
<main class="canvas">

  <section class="card card--front" aria-label="Business card front">
    <div class="front-pattern" role="img" aria-label="Repeating pattern of cakes, cupcakes, doughnuts, cookies and pretzels in soft pink"></div>
    <div class="front-badge"></div>
    <div class="front-badge__content">
      <span class="front-badge__mark"></span>
      <p class="front-badge__name">Tarts and Treats<br>by Maren</p>
    </div>
  </section>

  <section class="card card--back" aria-label="Business card back">
    <p class="back-mobile">Mobile: 0492 815 063</p>

    <div class="brand">
      <span class="brand__mark"></span>
      <p class="brand__name">Tarts and Treats</p>
      <p class="brand__byline">
        <span class="brand__rule"></span>
        <span>by Maren</span>
        <span class="brand__rule"></span>
      </p>
    </div>

    <footer class="contact-band">
      <span class="contact-item">
        <svg width="16" height="12" viewBox="0 0 16 12" aria-hidden="true">
          <rect x="0.5" y="0.5" width="15" height="11" rx="1" fill="#fff"/>
          <path d="M1 1.5 L8 7 L15 1.5" fill="none" stroke="#e667a6" stroke-width="1.4"/>
        </svg>
        maren@tartsandtreatsbymaren.example.au
      </span>
      <span class="contact-item">
        <span class="contact-item__dot"></span>
        instagram.com/tartsandtreatsbymaren/
      </span>
      <span class="contact-item">
        <span class="contact-item__dot"></span>
        fb.me/tartsandtreatsbymaren
      </span>
    </footer>
  </section>

</main>
</body>
</html>
```